Harbourline Physiotherapy business card design

We need a fresh, new business card design for our physiotherapy clinic Harbourline Physiotherapy

Will attach logo soon we had logo designed from our last project

Industry/Entity Type

Physical Therapy

Contact Information for Business Card

On front
Needs our logo, contact details:
58 Wexley Lane Marrowvale NSW 2781
Ph/f: 02 9481 2057
info@harbourlinephysio.example.com.au

Requirements
Must have
• On the back of the card needs to have area to write down follow up appointments
• On front
• Needs our logo
• The colours have to be the colours in our logo which are: sky blue, black and white
• Font to be same as our logo please
• We want the card to look simple, not too cluttered but to the point
Should not have
• We don't need any extra pictures other than our logo

```html
<!DOCTYPE html>
<html lang="en">
<head>
<meta charset="utf-8">
<title>Harbourline Physiotherapy – Business Card</title>
<link href="https://fonts.googleapis.com/css2?family=Open+Sans:ital,wght@0,400;0,600;0,700;1,400&display=swap" rel="stylesheet">
<style>
  :root{
    --page:#e9e9ec;
    --paper:#ffffff;
    --blue-deep:#2a2f9e;
    --blue-mid:#2f5fd0;
    --blue-bright:#3b8ff0;
    --navy:#1f2a8a;
    --grey-swoosh:#6e6e74;
    --ink:#3a3a40;
    --ink-soft:#6a6a72;
    --title-blue:#2a47b8;
  }
  *{box-sizing:border-box;margin:0;padding:0}
  html,body{width:1200px;height:950px;overflow:hidden}
  body{background:var(--page);font-family:"Open Sans",Arial,sans-serif;position:relative}
  .card{position:absolute;left:220px;width:760px;height:434px;background:var(--paper);
    box-shadow:0 6px 18px rgba(0,0,0,.18);overflow:hidden}
  .card--front{top:30px}
  .card--back{top:490px}

  /* front */
  .front-art{position:absolute;inset:0;width:100%;height:100%}
  .brand{position:absolute;left:46px;top:250px;display:flex;align-items:center;gap:14px}
  .brand-dot{width:34px;height:34px;border-radius:50%;background:var(--blue-mid)}
  .brand-name{font-weight:600;font-size:27px;line-height:1.1;color:var(--blue-mid);width:200px}
  .contact{position:absolute;right:38px;top:34px;text-align:right;color:#fff}
  .contact-name{font-size:25px;font-weight:600;line-height:1.1}
  .contact-role{font-size:16px;margin-bottom:26px}
  .contact-line{font-size:16px;line-height:1.55;display:flex;justify-content:flex-end;align-items:center;gap:10px}
  .contact-line svg{width:16px;height:16px;fill:#fff;flex:none}
  .contact-line--address{margin-bottom:14px}
  .contact-line--web{margin-top:22px}
  .spacer{width:16px;flex:none}

  /* back */
  .appt{position:absolute;inset:44px 52px;color:var(--ink)}
  .appt-title{font-size:28px;font-weight:700;color:var(--title-blue);text-align:right;margin-bottom:22px}
  .appt-row{display:flex;align-items:flex-end;gap:10px;font-size:18px;margin-bottom:30px}
  .dots{flex:1;border-bottom:2px dotted var(--ink-soft);height:20px}
  .dots--short{flex:0 0 260px}
  .appt-label{color:var(--ink)}
  .ampm{font-size:15px;color:var(--title-blue)}
  .days{display:flex;justify-content:space-between;font-size:18px;color:var(--title-blue);margin-bottom:34px}
  .day{display:flex;align-items:center;gap:7px}
  .box{width:16px;height:16px;border:1.6px solid var(--ink)}
  .notice{font-size:14px;font-style:italic;color:var(--ink-soft);line-height:1.5;max-width:560px}
</style>
</head>
<body>

<section class="card card--front" aria-label="Business card front">
  <svg class="front-art" viewBox="0 0 760 434" preserveAspectRatio="none" aria-hidden="true">
    <defs>
      <radialGradient id="blueField" cx="0.7" cy="0.35" r="0.75">
        <stop offset="0" stop-color="#3b8ff0"/>
        <stop offset="0.55" stop-color="#2f5fd0"/>
        <stop offset="1" stop-color="#2a2f9e"/>
      </radialGradient>
    </defs>
    <path d="M232 0 C300 120 226 232 350 336 C420 392 500 424 580 434 L760 434 L760 0 Z" fill="#6e6e74"/>
    <path d="M252 0 C322 118 246 228 370 330 C440 386 520 418 600 434 L760 434 L760 0 Z" fill="#1f2a8a"/>
    <path d="M262 0 C334 116 258 226 382 326 C452 380 532 414 612 434 L760 434 L760 0 Z" fill="url(#blueField)"/>
  </svg>

  <div class="brand">
    <span class="brand-dot"></span>
    <span class="brand-name">Harbourline Physiotherapy</span>
  </div>

  <div class="contact">
    <p class="contact-name">Daniel Archer</p>
    <p class="contact-role">CEO/Founder</p>
    <p class="contact-line contact-line--address">58 Wexley Lane Marrowvale<br>NSW 2781<span class="spacer"></span></p>
    <p class="contact-line">02 9481 2057
      <svg viewBox="0 0 24 24"><path d="M6.6 10.8a15.1 15.1 0 0 0 6.6 6.6l2.2-2.2a1 1 0 0 1 1-.25 11.4 11.4 0 0 0 3.6.57 1 1 0 0 1 1 1V20a1 1 0 0 1-1 1A17 17 0 0 1 3 4a1 1 0 0 1 1-1h3.5a1 1 0 0 1 1 1c0 1.25.2 2.45.57 3.6a1 1 0 0 1-.25 1z"/></svg></p>
    <p class="contact-line">02 9481 2058
      <svg viewBox="0 0 24 24"><path d="M7 3h10v5H7zM4 9h16a2 2 0 0 1 2 2v6h-4v4H6v-4H2v-6a2 2 0 0 1 2-2zm4 7v3h8v-3z"/></svg></p>
    <p class="contact-line contact-line--web">info@harbourlinephysio.example.com.au
      <svg viewBox="0 0 24 24"><path d="M3 5h18v14H3zm2 2v.4l7 4.6 7-4.6V7z"/></svg></p>
    <p class="contact-line">www.harbourlinephysio.example.com.au
      <svg viewBox="0 0 24 24"><path d="M12 2a10 10 0 1 0 0 20 10 10 0 0 0 0-20zm6.9 9h-3a15 15 0 0 0-1.3-5.6A8 8 0 0 1 18.9 11zM12 4.1c.9 1.3 1.7 3.6 1.9 6.9h-3.8c.2-3.3 1-5.6 1.9-6.9zM9.4 5.4A15 15 0 0 0 8.1 11h-3a8 8 0 0 1 4.3-5.6zM5.1 13h3a15 15 0 0 0 1.3 5.6A8 8 0 0 1 5.1 13zm6.9 6.9c-.9-1.3-1.7-3.6-1.9-6.9h3.8c-.2 3.3-1 5.6-1.9 6.9zm2.6-1.3a15 15 0 0 0 1.3-5.6h3a8 8 0 0 1-4.3 5.6z"/></svg></p>
  </div>
</section>

<section class="card card--back" aria-label="Business card back">
  <div class="appt">
    <h2 class="appt-title">Next Appointment</h2>
    <div class="appt-row"><span class="dots"></span><span class="appt-label">has an appointment</span></div>
    <div class="appt-row"><span class="appt-label">Time :</span><span class="dots dots--short"></span><span class="ampm">AM/PM</span></div>
    <div class="days">
      <span class="day">Mon <span class="box"></span></span>
      <span class="day">Tue <span class="box"></span></span>
      <span class="day">Wed <span class="box"></span></span>
      <span class="day">Thu <span class="box"></span></span>
      <span class="day">Fri <span class="box"></span></span>
      <span class="day">Sat <span class="box"></span></span>
    </div>
    <p class="notice">Please give 24 hours notice if you are unable to keep your appointment or a cancellation fee may be charged.</p>
  </div>
</section>

</body>
</html>
```